AMBER AND SLATE WEB

We need a home design in wordpress, we have now a web but we would like to improve it. Our current web is www.amberandslatevillas.example Our business is holliday rental of villas in Ibiza. Our guest must know that we are a reliable company, professional and with experience and good reviews. We want them to click in our reservation engine: https://bookings.amberandslatevillas.example/en/ and make reservation in our website. We would also like to say that all the properties that we have are just us who commercialize so we have best price available. Many people are going to see our villas in staylist.example and look to our website to make a reservation with us so we need to show them that they are at the right place and click at our link to our reservation engine. What make us special is that we are a local company, we are from Ibiza, Our guests are always received in person by the Amber and Slate Ibiza team. You will enjoy extensive tourist information when you check in and during the entire stay. You will be attended by ChatterLine and calls, always happy to help so that you have a happy and fun stay! Our guest stay is better than in hotel as they have more spece, private swiming pool, private garden, barbeque ... To rent a villa is the best way to stay in Ibiza. We also have a promotional video: https://vidshare.example/Qm7TzR2pLxA Let our philosophy be shown, we think that coming on holiday to Ibiza implies seeing the nature that we have in Ibiza, hence our name AMBER AND SLATE, like the pins that almost touch the sea in Ibiza, or the posidonea meadows where the intense green of the seaweed and the blue of the sea. We are aware of the environment, and we love Ibiza. For us, the client who visits Ibiza, should rent a car, go around the island, eat in a restaurant one day in front of the sea, is a night of partying to the discs, go shopping, visit the ancient heritage of Umanity, make some aquatic sport, enjoy the pool, those are for us Ibiza.

Target Market(s)

Europe, people from Holand, UK, Germany, France, Spain ...

Industry/Entity Type

Tourism

Colors

Designer to choose colors to be used in the design.

Requirements
Must have
• Pictures of Ibiza.
Nice to have
• Our name Amber and Slate Ibiza is beacuse in Ibiza there is forest that almost touch the watter of the Mediterranean sea, so you can see green of the forest and blue of the sea and the sky. And also beacause under the watter of the sea there is a plant called Posidonia that is also green please see the picture of posidonia.

```html
<!DOCTYPE html>
<html lang="en">
<head>
<meta charset="utf-8">
<title>Amber and Slate Villas Ibiza</title>
<link href="https://fonts.googleapis.com/css2?family=Roboto:wght@300;400;500;700;900&family=Poppins:wght@400;500;600&family=Crimson+Text&display=swap" rel="stylesheet">
<style>
:root{
  --green:#5e9237;
  --green-dark:#3f7a2c;
  --blue:#2a8fd0;
  --navy:#1a2330;
  --ink:#1d1d1d;
  --text:#555;
  --light:#f4f4f4;
  --white:#fff;
  --footer:#151c22;
}
*{box-sizing:border-box;margin:0;padding:0}
html,body{width:1200px;height:4591px;overflow:hidden}
body{font-family:"Poppins",sans-serif;color:var(--text);background:var(--white);position:relative}
.abs{position:absolute}
a{color:inherit;text-decoration:none}

.topbar{top:0;left:0;width:1200px;height:30px;background:linear-gradient(90deg,var(--green-dark),var(--blue));color:#fff;font-size:14px;display:flex;align-items:center;justify-content:flex-end;gap:26px;padding-right:100px}
.topbar span{display:flex;align-items:center;gap:8px}
.nav{top:30px;left:0;width:1200px;height:98px;background:#fff;display:flex;align-items:center;padding:0 100px}
.brand{display:flex;align-items:center;gap:10px;font-family:"Roboto",sans-serif;font-weight:500;font-size:27px;color:var(--green);letter-spacing:.5px}
.brand i{width:22px;height:22px;border-radius:50%;background:var(--green);display:block}
.menu{margin-left:auto;display:flex;gap:22px;align-items:center;font-family:"Roboto",sans-serif;font-weight:500;font-size:15px;color:#222}
.menu .book{background:var(--blue);color:#fff;padding:6px 23px}

.hero{top:128px;left:0;width:1200px;height:662px;background:linear-gradient(180deg,#1f5fa8 0%,#3a86c6 30%,#2d6a4a 62%,#3fb3b0 85%,#c9b58c 100%)}
.hero-title{top:200px;width:1200px;text-align:center;color:#fff;font-family:"Roboto",sans-serif}
.hero-title .l1{font-weight:300;font-size:70px;line-height:80px}
.hero-title .l2{font-weight:900;font-size:72px;line-height:80px}
.hero-btn{top:383px;left:505px;width:192px;height:44px;border:2px solid #fff;border-radius:22px;color:#fff;font-family:"Roboto",sans-serif;font-weight:700;font-size:16px;display:flex;align-items:center;justify-content:center}
.arrow{top:296px;width:36px;height:36px;border-radius:50%;background:rgba(0,0,0,.45);display:flex;align-items:center;justify-content:center}

.booking{top:686px;left:134px;width:932px;height:139px;background:rgba(20,20,20,.9);border-radius:3px}
.booking h3{text-align:center;color:#fff;font-family:"Roboto",sans-serif;font-weight:700;font-size:27px;margin-top:26px}
.fields{display:flex;gap:12px;padding:14px 14px 0 14px}
.field{height:36px;background:#fff;border-radius:2px;font-size:11px;color:#444;display:flex;align-items:center;justify-content:space-between;padding:0 12px;width:206px}
.search{width:32px;height:32px;border-radius:50%;background:var(--blue);margin-top:2px;display:flex;align-items:center;justify-content:center}

.sec-title{width:1200px;text-align:center;font-family:"Roboto",sans-serif;font-size:37px;color:var(--ink);font-weight:400}
.sec-title b{font-weight:700}
.divider{left:499px;width:202px;height:16px;display:flex;align-items:center;gap:8px}
.divider span{flex:1;height:2px;background:var(--green)}
.divider i{width:12px;height:16px;border-radius:50%;background:var(--green);display:block}

.rentals{top:790px;left:0;width:1200px;height:833px;background:var(--light)}
.side-tree{width:62px;height:180px;background:linear-gradient(180deg,#7fb446,#2f6b25)}
.card{top:1072px;width:294px;height:411px;background:#fff;box-shadow:0 2px 6px rgba(0,0,0,.08);text-align:center}
.card .ph{height:235px}
.card .badge{width:30px;height:30px;border-radius:50%;background:#fff;margin:-16px auto 0;display:flex;align-items:center;justify-content:center}
.card .badge i{width:14px;height:18px;border-radius:50%;background:var(--green);display:block}
.card h4{font-family:"Roboto",sans-serif;font-weight:400;font-size:19px;color:#222;margin-top:10px}
.card p{font-size:12.5px;line-height:21px;margin:10px 22px 0}
.card .btn{position:absolute;left:89px;bottom:-14px;width:116px;height:30px;background:var(--blue);color:#fff;font-family:"Roboto",sans-serif;font-weight:500;font-size:13px;display:flex;align-items:center;justify-content:center}

.video{top:1876px;left:134px;width:456px;height:321px;background:#fff;box-shadow:0 16px 22px -14px rgba(0,0,0,.35)}
.video .ph{height:290px;background:linear-gradient(135deg,#b5864a,#6e7b4a 45%,#4aa5d8 75%,#2d3a46)}
.play{position:absolute;left:200px;top:119px;width:52px;height:52px;border-radius:50%;background:rgba(0,0,0,.55);border:2px solid #fff;display:flex;align-items:center;justify-content:center}
.ctrl{height:31px;display:flex;align-items:center;gap:10px;padding:0 8px;font-size:8px;color:#333}
.ctrl .bar{height:3px;background:#ddd;flex:1;position:relative}
.ctrl .bar::before{content:"";position:absolute;left:0;top:0;height:3px;width:45%;background:#e03c31}
.welcome-text{top:1876px;left:633px;width:432px;font-size:14px;line-height:30px}
.welcome-text p+p{margin-top:10px}
.outline-btn{border:2px solid #333;color:#222;font-family:"Roboto",sans-serif;font-weight:500;font-size:14px;display:inline-flex;align-items:center;justify-content:center;width:126px;height:40px}

.services{top:2345px;left:0;width:1200px;height:652px;background:linear-gradient(100deg,#2a88c8 0%,#3a94b0 45%,#4a8f5c 80%,#3f7a3a 100%)}
.services .sec-title{color:#fff}
.svc{width:220px;text-align:center;color:#fff;font-family:"Roboto",sans-serif;font-weight:500;font-size:13.5px;line-height:24px}
.svc .ic{width:80px;height:80px;border-radius:50%;border:2px solid #fff;margin:0 auto 14px;display:flex;align-items:center;justify-content:center}

.philo{top:2997px;left:0;width:1200px;height:550px;background:linear-gradient(100deg,#1c6fb0 0%,#2f9fc8 35%,#7fcfd0 55%,#dcc8a0 75%,#caa77a 100%)}
.philo-box{top:3047px;left:601px;width:465px;height:446px;background:rgba(255,255,255,.93);padding:44px 42px}
.philo-box h2{font-family:"Roboto",sans-serif;font-weight:700;font-size:37px;color:var(--ink)}
.philo-box p{font-size:14px;line-height:30px;margin-top:46px}

.quote{top:3780px;width:289px;height:228px;background:#fff;box-shadow:0 4px 14px rgba(0,0,0,.14);text-align:center;font-family:"Crimson Text",serif;color:#444}
.quote .mark{font-size:48px;color:var(--green);line-height:40px;margin-top:36px;font-family:Georgia,serif}
.quote p{font-size:13px;line-height:25px;margin:10px 18px 0}
.quote .who{font-size:15px;margin-top:14px}

.footer{top:4128px;left:0;width:1200px;height:463px;background:linear-gradient(180deg,#1a242c,#11171c)}
.footer h5{font-family:"Roboto",sans-serif;font-weight:700;font-size:21px;color:#fff}
.links{list-style:none;font-size:12.5px;color:#ddd;line-height:24px;margin-top:14px}
.links li::before{content:"›";margin-right:12px}
.input{height:40px;border:1px solid #aaa;color:#ddd;font-size:10px;display:flex;align-items:center;padding-left:12px}
.submit{height:38px;background:var(--blue);color:#fff;font-family:"Roboto",sans-serif;font-weight:700;font-size:15px;display:flex;align-items:center;justify-content:center}
.contact{font-size:13px;color:#ddd;line-height:19px}
.contact div{display:flex;gap:16px;margin-top:14px}
.bottom{top:4493px;left:0;width:1200px;height:98px;border-top:1px solid rgba(255,255,255,.08);font-size:12.5px;color:#ddd}
.soc{width:22px;height:22px;border:1px solid #ddd;border-radius:50%}
</style>
</head>
<body>

<div class="abs topbar">
  <span><svg width="13" height="13" viewBox="0 0 24 24" fill="#fff"><path d="M6.6 10.8a15 15 0 006.6 6.6l2.2-2.2a1 1 0 011-.25 11 11 0 003.5.56 1 1 0 011 1V20a1 1 0 01-1 1A17 17 0 013 4a1 1 0 011-1h3.5a1 1 0 011 1 11 11 0 00.56 3.5 1 1 0 01-.25 1z"/></svg>+34600123456</span>
  <span><svg width="15" height="12" viewBox="0 0 24 18" fill="none" stroke="#fff" stroke-width="2"><rect x="1" y="1" width="22" height="16"/><path d="M1 1l11 9 11-9"/></svg>info@amberandslateibiza.example</span>
  <span style="font-size:11px;font-weight:500">ENGLISH ⌄</span>
</div>

<header class="abs nav">
  <div class="brand"><i></i>AMBER AND SLATE</div>
  <nav class="menu">
    <a>HOME</a><a>EXPERIENCE</a><a>ABOUT US</a><a>ALL PROPERTIES</a><a>CONTACT</a><a class="book">BOOK</a>
  </nav>
</header>

<section class="abs hero" role="img" aria-label="Photo of an Ibiza cove with pine-covered cliffs, turquoise water and a sandy beach"></section>
<div class="abs arrow" style="left:74px"><svg width="10" height="16" viewBox="0 0 10 16"><path d="M8 1L2 8l6 7" stroke="#fff" stroke-width="1.6" fill="none"/></svg></div>
<div class="abs arrow" style="left:1090px"><svg width="10" height="16" viewBox="0 0 10 16"><path d="M2 1l6 7-6 7" stroke="#fff" stroke-width="1.6" fill="none"/></svg></div>
<div class="abs hero-title"><div class="l1">The best way</div><div class="l2">TO STAY IN IBIZA!</div></div>
<a class="abs hero-btn">GET MORE INFO</a>

<div class="abs booking">
  <h3>BOOKING YOUR TRIP</h3>
  <div class="fields">
    <div class="field">Where do you want to go? <span>▾</span></div>
    <div class="field">Date of Journey <span>▦</span></div>
    <div class="field">Date of Return <span>▦</span></div>
    <div class="field">Location <svg width="9" height="12" viewBox="0 0 12 16"><path d="M6 0a6 6 0 00-6 6c0 4.5 6 10 6 10s6-5.5 6-10a6 6 0 00-6-6zm0 8.5A2.5 2.5 0 118.5 6 2.5 2.5 0 016 8.5z" fill="#333"/></svg></div>
    <div class="search"><svg width="12" height="12" viewBox="0 0 16 16"><circle cx="6.5" cy="6.5" r="5" stroke="#fff" stroke-width="2" fill="none"/><path d="M10 10l5 5" stroke="#fff" stroke-width="2"/></svg></div>
  </div>
</div>

<section class="abs rentals"></section>
<div class="abs side-tree" style="left:0;top:1443px" role="img" aria-label="Pine tree decoration"></div>
<div class="abs side-tree" style="left:1138px;top:1443px" role="img" aria-label="Pine tree decoration"></div>
<h2 class="abs sec-title" style="top:915px"><b>HOLIDAY RENTAL</b> OF VILLAS IN IBIZA</h2>
<div class="abs divider" style="top:997px"><span></span><i></i><span></span></div>

<article class="abs card" style="left:134px">
  <div class="ph" role="img" aria-label="Photo of a sunny Ibiza beach with parasols" style="background:linear-gradient(180deg,#5a9fd8,#3aa0b8 45%,#e0c48c)"></div>
  <div class="badge"><i></i></div>
  <h4>Nemo enim ipsam volupta</h4>
  <p>Sed ut perspiciatis unde omnis iste natus voluptatem accusantium doloremque laudantium, totam rem</p>
  <a class="btn">VIEW DETAILS</a>
</article>
<article class="abs card" style="left:453px">
  <div class="ph" role="img" aria-label="Photo of a parasol and sun loungers on a lawn" style="background:linear-gradient(180deg,#4a88c8,#8fb4d0 45%,#4f7a36)"></div>
  <div class="badge"><i></i></div>
  <h4>Nemo enim ipsam volupta</h4>
  <p>Sed ut perspiciatis unde omnis iste natus voluptatem accusantium doloremque laudantium, totam rem</p>
  <a class="btn">VIEW DETAILS</a>
</article>
<article class="abs card" style="left:774px">
  <div class="ph" role="img" aria-label="Underwater photo of a posidonia seagrass meadow" style="background:linear-gradient(180deg,#1e7fb0,#2fa0a0 50%,#3f8a2a)"></div>
  <div class="badge"><i></i></div>
  <h4>Nemo enim ipsam volupta</h4>
  <p>Sed ut perspiciatis unde omnis iste natus voluptatem accusantium doloremque laudantium, totam rem</p>
  <a class="btn">VIEW DETAILS</a>
</article>

<h2 class="abs sec-title" style="top:1710px"><b>WELCOME TO</b> AMBER AND SLATE VILLAS IBIZA</h2>
<div class="abs divider" style="top:1792px"><span></span><i></i><span></span></div>

<div class="abs video">
  <div class="ph" role="img" aria-label="Promotional video still of a villa swimming pool"></div>
  <div class="play"><svg width="16" height="18" viewBox="0 0 16 18"><path d="M2 1l13 8-13 8z" fill="none" stroke="#fff" stroke-width="2"/></svg></div>
  <div class="ctrl"><span>▶</span><span>0:00/0:03</span><div class="bar"></div><span>🔈</span><div style="width:40px;height:3px;background:#e03c31"></div></div>
</div>
<div class="abs welcome-text">
  <p>Sed ut perspiciatis unde omnis iste natus error sit votem accusantium doloremque laudantium, totam rem apam, eaque ipsa quae ab illo inventore veritatis et quasi arcto beatae vitae dicta sunt explicabo. Nemo enim ipsam vm quia voluptas sit aspernatur aut odit aut fugit, sed quia consequuntur magni dolores eos qui ratione voltatem sequi nesciunt. Neque porro quisquam</p>
  <p>Nemo enim ipsam vm quia voluptas sit aspernatur aut odit aut fugit, sed quia consequuntur magni dolores eos qui</p>
  <a class="outline-btn" style="margin-top:22px">READ MORE</a>
</div>

<section class="abs services" role="img" aria-label="Photo of Ibiza coastline and sea behind a blue-green overlay"></section>
<h2 class="abs sec-title" style="top:2427px;color:#fff"><b>IBIZA</b> SERVICES</h2>
<div class="abs divider" style="top:2508px"><span style="background:#fff"></span><i style="background:#fff"></i><span style="background:#fff"></span></div>

<div class="abs svc" style="left:127px;top:2574px"><div class="ic" role="img" aria-label="Car icon"></div>RENT A CAR</div>
<div class="abs svc" style="left:341px;top:2574px"><div class="ic" role="img" aria-label="Island icon"></div>GO AROUND THE ISLAND</div>
<div class="abs svc" style="left:580px;top:2574px"><div class="ic" role="img" aria-label="Restaurant icon"></div>EAT IN A RESTAURANT ONE<br>DAY IN FRONT OF THE SEA</div>
<div class="abs svc" style="left:815px;top:2574px"><div class="ic" role="img" aria-label="Party icon"></div>IS A NIGHT OF PARTYING<br>TO THE DISCOS</div>
<div class="abs svc" style="left:127px;top:2758px"><div class="ic" role="img" aria-label="Shopping bag icon"></div>GO SHOPPING</div>
<div class="abs svc" style="left:341px;top:2758px"><div class="ic" role="img" aria-label="Heritage icon"></div>VISIT THE ANCIENT HERITAGE<br>OF HUMANITY</div>
<div class="abs svc" style="left:580px;top:2758px"><div class="ic" role="img" aria-label="Aquatic sport icon"></div>MAKE SOME AQUATIC<br>SPORT</div>
<div class="abs svc" style="left:815px;top:2758px"><div class="ic" role="img" aria-label="Swimming pool icon"></div>ENJOY THE POOL</div>

<section class="abs philo" role="img" aria-label="Photo of a turquoise Ibiza bay with rocks and a sandy shore"></section>
<div class="abs philo-box">
  <h2>OUR PHILOSOPHY</h2>
  <div class="divider" style="position:absolute;left:47px;top:112px;width:150px"><span></span><i></i><span></span></div>
  <p>Sed ut perspiciatis unde omnis iste natus error sit votem accusantium doloremque laudantium, totam rem apam, eaque ipsa quae ab illo inventore veritatis et quasi arcto beatae vitae dicta sunt explicabo. Nemo enim ipsam vm quia voluptas sit aspernatur aut odit aut fugit, sed quia consequuntur magni dolores eos qui ratione voltatem sequi nesciunt. Neque porro quisquam</p>
  <a class="outline-btn" style="margin-top:20px">READ MORE</a>
</div>

<h2 class="abs sec-title" style="top:3623px"><b>WHAT PEOPLE</b> ARE SAYING</h2>
<div class="abs divider" style="top:3702px"><span></span><i></i><span></span></div>

<div class="abs quote" style="left:128px"><div class="mark">“</div><p>Nemo enim ipsam vptatem quia vtas sit aspernatur aut odit aut fugit, sed quia contur magni dolores eos qui ratione Nemo enim ipsam vptatem quia vtas sit</p><div class="who">-Marlow T.</div></div>
<div class="abs quote" style="left:451px"><div class="mark">“</div><p>Nemo enim ipsam vptatem quia vtas sit aspernatur aut odit aut fugit, sed quia contur magni dolores eos qui ratione Nemo enim ipsam vptatem quia vtas sit</p><div class="who">-Marlow T.</div></div>
<div class="abs quote" style="left:774px"><div class="mark">“</div><p>Nemo enim ipsam vptatem quia vtas sit aspernatur aut odit aut fugit, sed quia contur magni dolores eos qui ratione Nemo enim ipsam vptatem quia vtas sit</p><div class="who">-Marlow T.</div></div>

<footer class="abs footer"></footer>
<div class="abs" style="left:136px;top:4200px">
  <h5>QUICK LINKS</h5>
  <ul class="links"><li>Home</li><li>Experience</li><li>All Properties</li><li>About Us</li><li>Contact Us</li><li>Book</li></ul>
</div>
<div class="abs" style="left:350px;top:4200px;width:436px">
  <h5>GET A QUOTE</h5>
  <p style="font-size:11px;color:#ddd;line-height:19px;margin-top:16px">Lorem ipsum dolor sit amet, consectetur adipiscing elit, sed do eiusmod tempor incididunt ut labore et dolore magna aliqua.</p>
  <div style="display:grid;grid-template-columns:212px 212px;gap:10px;margin-top:14px">
    <div class="input">Name</div><div class="input">E - Mail</div>
    <div class="input">Phone No</div><div class="submit">SUBMIT</div>
  </div>
</div>
<div class="abs contact" style="left:854px;top:4200px;width:240px">
  <h5>CONTACT US</h5>
  <div><svg width="12" height="16" viewBox="0 0 12 16"><path d="M6 0a6 6 0 00-6 6c0 4.5 6 10 6 10s6-5.5 6-10a6 6 0 00-6-6zm0 8.5A2.5 2.5 0 118.5 6 2.5 2.5 0 016 8.5z" fill="#ddd"/></svg><span>Amber and Slate Villas Ibiza<br>12 Harbour Lane,<br>Sample Town 00000</span></div>
  <div><svg width="12" height="12" viewBox="0 0 24 24" fill="#ddd"><path d="M6.6 10.8a15 15 0 006.6 6.6l2.2-2.2a1 1 0 011-.25 11 11 0 003.5.56 1 1 0 011 1V20a1 1 0 01-1 1A17 17 0 013 4a1 1 0 011-1h3.5a1 1 0 011 1 11 11 0 00.56 3.5 1 1 0 01-.25 1z"/></svg><span>+34600123456</span></div>
  <div><svg width="12" height="10" viewBox="0 0 24 18" fill="#ddd"><rect width="24" height="18"/></svg><span>info@amberandslateibiza.example</span></div>
</div>
<div class="abs bottom">
  <span style="position:absolute;left:132px;top:42px">© 2019 Amber and Slate Villas Ibiza. All Rights Reserved.</span>
  <div style="position:absolute;left:967px;top:38px;display:flex;gap:6px"><i class="soc"></i><i class="soc"></i><i class="soc"></i><i class="soc"></i></div>
</div>

</body>
</html>
```